Business Card Design Project

Business Card design based on logo.
Updates

I need business card, letterhead, envelope, and if possible, Powerpoint slide template.

On front of business card: Just logo- and  my name and title:  Harriet Lindqvist, Principal

On reverse-logo and the rest of the contact info:

4871 Quarry Lane
Alder Falls, OR 97871
555-318-2764
hl@brackenstudyworks.example

On letterhead-Just logo at top, at bottom  the rest-very small along the bottom

On PPT slide-just the logo.

I also want to try a few other colors-I like lime/dark grey (not black) but would like to try Sienna, maybe also indigo or bright blue-green.

I forgot to add-

On the business card-switch to vertical on reverse side and put:

Reverse side-switch to vertical and list:

Harriet Lindqvist
Principal
Bracken Study Works, LLC

555-318-2764

4871 Quarry Lane
Alder Falls, OR 97871

Harriet Lindqvist
Principal

555-318-2764

4871 Quarry Lane
Alder Falls, OR 97871

I have another project at the same time-for Stationery. Feel free to submit to that one also.

That one includes letterhead, envelope, PPT slide, folder cover sheet-HL

Industry/Entity Type

Business

Requirements
Must have
• Must use logo-preferably lime green version-with gray, not black or just 2-tone -logo on colored background.

```html
<!DOCTYPE html>
<html lang="en">
<head>
<meta charset="utf-8">
<title>Bracken Study Works – Business Card</title>
<link rel="stylesheet" href="https://fonts.googleapis.com/css2?family=Source+Sans+3:wght@400;600&display=swap">
<style>
  :root {
    --page: #ebebeb;
    --card-light: #e4e4e4;
    --lime: #7ba428;
    --charcoal-top: #2b2b2b;
    --charcoal-bottom: #141414;
    --ink-dark: #333333;
    --ink-light: #ececec;
  }
  html, body {
    margin: 0;
    width: 1200px;
    height: 1192px;
    overflow: hidden;
    background: var(--page);
    font-family: "Source Sans 3", sans-serif;
  }
  .canvas { position: relative; width: 1200px; height: 1192px; }
  .card { position: absolute; top: 256px; height: 653px; overflow: hidden; }
  .card--front { left: 179px; width: 364px; background: var(--card-light); }
  .card--back {
    left: 670px; width: 371px;
    background: linear-gradient(160deg, var(--charcoal-top), var(--charcoal-bottom));
  }
  .brand {
    position: absolute; left: 0; right: 0;
    text-align: center;
    font-weight: 400;
    font-size: 36px;
    line-height: 1.15;
    letter-spacing: 4px;
    text-transform: uppercase;
  }
  .card--front .brand { top: 153px; color: var(--ink-dark); }
  .card--back .brand { top: 338px; color: var(--ink-light); }
  .name-band {
    position: absolute; left: 0; right: 0; top: 310px; height: 97px;
    background: var(--lime);
    color: #fff;
    padding: 24px 0 0 31px;
    box-sizing: border-box;
  }
  .name-band .person { font-weight: 600; font-size: 21px; line-height: 26px; }
  .name-band .role { font-size: 18px; line-height: 24px; opacity: .95; }
  .contact-panel {
    position: absolute; left: 0; right: 0; top: 407px; bottom: 0;
    background: linear-gradient(160deg, var(--charcoal-top), var(--charcoal-bottom));
    color: var(--ink-light);
    font-size: 17px;
  }
  .contact-row { position: absolute; left: 64px; line-height: 26px; }
  .contact-icon { position: absolute; left: 30px; }
  .web {
    position: absolute; left: 0; right: 0; top: 548px;
    text-align: center; color: var(--ink-light); font-size: 18px;
  }
</style>
</head>
<body>
<main class="canvas">
  <section class="card card--front" aria-label="Business card front">
    <div class="brand">Bracken<br>Study Works</div>
    <div class="name-band">
      <div class="person">Harriet Lindqvist</div>
      <div class="role">Principal</div>
    </div>
    <div class="contact-panel">
      <svg class="contact-icon" style="top:49px" width="18" height="18" viewBox="0 0 18 18" aria-hidden="true">
        <circle cx="9" cy="9" r="9" fill="var(--lime)"/>
        <path d="M9 4a3 3 0 0 1 3 3c0 2.2-3 6-3 6s-3-3.8-3-6a3 3 0 0 1 3-3z" fill="#fff"/>
        <circle cx="9" cy="7" r="1.1" fill="var(--lime)"/>
      </svg>
      <div class="contact-row" style="top:43px">Bracken Study Works, LLC<br>4871 Quarry Lane, Alder Falls, OR 97871</div>
      <svg class="contact-icon" style="top:122px" width="18" height="18" viewBox="0 0 18 18" aria-hidden="true">
        <circle cx="9" cy="9" r="9" fill="var(--lime)"/>
        <path d="M5 7.5c0-1.5 8-1.5 8 0v1h-2V7.5H7v1H5zM6 9h6l1 4H5z" fill="#fff"/>
      </svg>
      <div class="contact-row" style="top:117px">555-318-2764</div>
      <svg class="contact-icon" style="top:148px" width="18" height="18" viewBox="0 0 18 18" aria-hidden="true">
        <circle cx="9" cy="9" r="9" fill="var(--lime)"/>
        <text x="9" y="12.5" text-anchor="middle" font-size="10" fill="#fff" font-family="Source Sans 3, sans-serif">@</text>
      </svg>
      <div class="contact-row" style="top:143px">hl@brackenstudyworks.example</div>
      <svg class="contact-icon" style="top:174px" width="18" height="18" viewBox="0 0 18 18" aria-hidden="true">
        <circle cx="9" cy="9" r="9" fill="var(--lime)"/>
        <g fill="none" stroke="#fff" stroke-width="1">
          <circle cx="9" cy="9" r="4.5"/>
          <ellipse cx="9" cy="9" rx="2" ry="4.5"/>
          <path d="M4.5 9h9"/>
        </g>
      </svg>
      <div class="contact-row" style="top:169px">www.brackenstudyworks.example</div>
    </div>
  </section>

  <section class="card card--back" aria-label="Business card back">
    <div class="brand">Bracken<br>Study Works</div>
    <div class="web">www.brackenstudyworks.example</div>
  </section>
</main>
</body>
</html>
```